Trueline Referral Hub needs updated website.

Our current website was designed on wix.com. (www.truelinereferralhub.example).
We would like something a little more customized for what our company offers. Trueline Referral Hub is a company specializing in connecting consumers with trustworthy and affordable service professionals. We need the website to be approachable and easy to use, while conveying our "Trueline" reputation.
Reason: Our project is now guaranteed. Please send your ideas. Thank you!
Target Market(s)
Homeowners
Industry/Entity Type
It Company
Look and feel
Each slider illustrates characteristics of the customer's brand and the style your logo design should communicate.

```html
<!DOCTYPE html>
<html lang="en">
<head>
<meta charset="utf-8">
<title>Trueline Referral Hub</title>
<link rel="stylesheet" href="https://fonts.googleapis.com/css2?family=Source+Sans+3:wght@400;600;700&display=swap">
<style>
:root{
  --navy:#131a3c;
  --navy-nav:#0f3a66;
  --blue:#2a7fd1;
  --ink:#1c2440;
  --text:#333a48;
  --muted:#8a8f98;
  --hero-bg:#e8eef3;
  --white:#ffffff;
  --rule:#d6d9de;
}
*{margin:0;padding:0;box-sizing:border-box}
html,body{width:716px;height:1200px;overflow:hidden;background:var(--white)}
body{font-family:"Source Sans 3",sans-serif;color:var(--text)}
.page{position:relative;width:716px;height:1200px;overflow:hidden}
.abs{position:absolute}

/* header */
.brand{left:63px;top:21px;display:flex;align-items:center;gap:8px}
.brand-dot{width:46px;height:46px;border-radius:50%;background:var(--blue)}
.brand-name{font-weight:700;font-size:28px;color:var(--navy-nav);letter-spacing:-.5px}
.header-address{left:393px;top:27px;font-size:9.5px;line-height:12px;color:var(--ink)}
.header-address .email{margin-top:7px}
.header-call{left:558px;top:27px;font-size:11px;color:var(--ink)}
.header-call strong{display:block;font-size:14.5px;font-weight:700;letter-spacing:.3px;margin-top:3px}

/* nav */
.nav-rule{left:0;top:92px;width:716px;height:1px;background:var(--navy-nav)}
.nav{left:0;top:92px;width:716px;height:41px}
.nav a{position:absolute;top:12px;font-size:13px;color:var(--ink);text-decoration:none;letter-spacing:.2px}
.nav .home{left:63px;top:0;width:99px;height:39px;background:var(--navy-nav);color:var(--white);font-weight:700;text-align:center;line-height:39px;border-bottom:2px solid var(--white);box-shadow:0 2px 0 var(--navy-nav)}

/* hero */
.hero{left:0;top:133px;width:716px;height:267px;background:var(--hero-bg)}
.hero-photo{left:302px;top:133px;width:414px;height:267px;background:linear-gradient(90deg,#dfe5ea 0%,#c9a58a 35%,#a9806a 60%,#e6ebef 100%)}
.hero-title{left:61px;top:166px;font-size:31px;line-height:37px;color:var(--ink);letter-spacing:1px;font-weight:400}
.hero-title b{color:var(--blue);font-weight:700}
.hero-copy{left:62px;top:285px;width:270px;font-size:11.3px;line-height:14.5px;color:var(--text)}
.hero-link{left:62px;top:323px;font-size:10.5px;color:var(--ink)}
.dots{left:62px;top:364px;display:flex;gap:4px}
.dots span{width:10px;height:10px;border-radius:50%;background:#b9bdc4}
.dots span:first-child{background:var(--navy-nav)}

/* intro */
.intro-title{left:0;top:415px;width:716px;text-align:center;font-size:21px;font-weight:700;color:var(--blue)}
.intro-sub{left:0;top:446px;width:716px;text-align:center;font-size:8.3px;color:var(--text)}

/* services band */
.band{left:0;top:474px;width:716px;height:293px;background:var(--navy)}
.band-active{left:101px;top:474px;width:163px;height:293px;background:var(--white)}
.service{top:474px;width:141px}
.service h3{margin-top:25px;font-size:11.5px;font-weight:700;color:var(--white);letter-spacing:.2px}
.service .thumb{margin-top:11px;height:103px}
.service p{margin-top:16px;font-size:7.8px;line-height:10.1px;color:var(--white)}
.service.is-active h3,.service.is-active p{color:var(--ink)}
.service .more{display:block;margin-top:13px;font-size:7.8px;font-weight:700;color:var(--ink)}
.heating{left:114px}
.heating .thumb{background:linear-gradient(180deg,#8a4f35 0%,#c9b6a4 45%,#d8d4cf 100%)}
.cooling{left:287px}
.cooling .thumb{background:linear-gradient(135deg,#e9ecef 0%,#bcc3ca 50%,#7aa7d8 100%)}
.auto{left:458px}
.auto .thumb{background:linear-gradient(135deg,#1d2a55 0%,#8d98aa 50%,#2b3f7a 100%)}
.arrow{top:605px;width:28px;height:34px;background:var(--white);display:flex;align-items:center;justify-content:center}
.arrow-prev{left:62px}
.arrow-next{left:624px}

/* about */
.about-title{left:62px;top:783px;font-size:29px;font-weight:700;color:var(--navy);letter-spacing:-.2px}
.about-lead{left:62px;top:823px;font-size:17px;line-height:21px;color:var(--ink)}
.about-lead span{color:var(--blue)}
.about-copy{left:62px;top:884px;width:360px;font-size:11.8px;line-height:15.5px;color:var(--text)}
.btn{left:62px;top:1011px;width:84px;height:32px;background:var(--blue);color:var(--white);font-size:12.5px;line-height:32px;text-align:center;text-decoration:none}
.divider{left:440px;top:783px;width:1px;height:262px;background:var(--rule)}

/* offers */
.offer-title{left:487px;top:782px;font-size:21px;font-weight:700;color:var(--navy)}
.offer{left:487px;display:flex;gap:6px}
.offer .pic{width:56px;height:56px;border:1px solid var(--rule);background:linear-gradient(180deg,#dfe8f1 0%,#b9c7d6 100%)}
.offer h4{font-size:8.3px;font-weight:400;color:var(--blue);letter-spacing:.2px}
.offer p{margin-top:5px;width:110px;font-size:7.6px;line-height:10.4px;color:var(--muted)}

/* footer */
.footer{left:0;top:1061px;width:716px;height:139px;background:var(--navy)}
.footer-brand{left:63px;top:1088px;display:flex;align-items:center;gap:6px}
.footer-brand .brand-dot{width:29px;height:29px;background:var(--white)}
.footer-brand .brand-name{font-size:18px;color:var(--white)}
.copyright{left:63px;top:1130px;font-size:8px;color:var(--white)}
.footer-links{right:63px;top:1082px;display:flex;gap:16px}
.footer-links a{font-size:8.3px;color:var(--white);text-decoration:none}
.footer-contact{right:63px;top:1108px;text-align:right;color:var(--white)}
.footer-contact .addr{font-size:11.2px}
.footer-contact .phone{margin-top:9px;font-size:14px;color:var(--blue)}
.footer-contact .mail{font-size:11.2px;margin-top:1px}
</style>
</head>
<body>
<div class="page">

  <header>
    <div class="abs brand"><span class="brand-dot"></span><span class="brand-name">Trueline</span></div>
    <div class="abs header-address">450 Harbor Lane, Saint<br>Louis, Missouri 63101<div class="email">E-mail: info@truelinereferralhub.example</div></div>
    <div class="abs header-call">Call Us Now:<strong>1 314 555 0142</strong></div>
  </header>

  <div class="abs nav-rule"></div>
  <nav class="abs nav">
    <a class="home" href="#">HOME</a>
    <a href="#" style="left:205px">ABOUT TRUELINE</a>
    <a href="#" style="left:356px">SERVICES</a>
    <a href="#" style="left:455px">OUR NETWORK</a>
    <a href="#" style="left:583px">CONTACT US</a>
  </nav>

  <section>
    <div class="abs hero"></div>
    <div class="abs hero-photo" role="img" aria-label="Photo of a smiling support agent wearing a headset"></div>
    <h1 class="abs hero-title">SOMETIMES ALL<br>YOU REALLY NEED<br><b>IS A TRUELINE</b></h1>
    <p class="abs hero-copy">Praesent vestibulum aenean nonummy hendrerit mauris. Hasellus porta. Fusce suscipit varius mi cum sociis</p>
    <div class="abs hero-link">LEARN MORE →</div>
    <div class="abs dots"><span></span><span></span><span></span><span></span></div>
  </section>

  <h2 class="abs intro-title">TRUELINE REFERRAL HUB</h2>
  <p class="abs intro-sub">Praesent vestibulum aenean nonummy hendrerit mauris. Hasellus porta. Fusce suscipit varius mi cum sociis natoque penatibus et magnis.</p>

  <section>
    <div class="abs band"></div>
    <div class="abs band-active"></div>
    <article class="abs service heating is-active">
      <h3>HEATING</h3>
      <div class="thumb" role="img" aria-label="Photo of an empty room with wooden ceiling and a heater"></div>
      <p>Praesent vestibulum aenean nonummy hendrerit mauris. Hasellus porta. Fusce suscipit varius mi cum sociis natoque penatibus et magnis dis parturient montes nascetur. sociis natoque penatibus et magnis dis parturient montes nascetur.</p>
      <span class="more">READ MORE</span>
    </article>
    <article class="abs service cooling">
      <h3>AIR CONDITIONING</h3>
      <div class="thumb" role="img" aria-label="Photo of an outdoor air conditioning unit fan"></div>
      <p>Praesent vestibulum aenean nonummy hendrerit mauris. Hasellus porta. Fusce suscipit varius mi cum sociis natoque penatibus et magnis dis parturient montes nascetur. sociis natoque penatibus et magnis dis parturient montes nascetur.</p>
    </article>
    <article class="abs service auto">
      <h3>AUTOMOTIVE MAINTENCE</h3>
      <div class="thumb" role="img" aria-label="Photo of chrome wrenches and mechanic tools"></div>
      <p>Praesent vestibulum aenean nonummy hendrerit mauris. Hasellus porta. Fusce suscipit varius mi cum sociis natoque penatibus et magnis dis parturient montes nascetur. sociis natoque penatibus et magnis dis parturient montes nascetur.</p>
    </article>
    <div class="abs arrow arrow-prev"><svg width="10" height="14" viewBox="0 0 10 14"><path d="M8 1 2 7l6 6" fill="none" stroke="#131a3c" stroke-width="2.6"/></svg></div>
    <div class="abs arrow arrow-next"><svg width="10" height="14" viewBox="0 0 10 14"><path d="M2 1l6 6-6 6" fill="none" stroke="#131a3c" stroke-width="2.6"/></svg></div>
  </section>

  <section>
    <h2 class="abs about-title">Trueline Referral Hub</h2>
    <p class="abs about-lead"><span>Connecting YOU</span> with the most reputable<br>and affordable businesses in Saint Louis.</p>
    <p class="abs about-copy">The founders of Trueline Referral Hub have over 30 years in the St. Louis Automotive and HVAC industries. In both markets, among many others, one thing is clear: A consumer gets better service at a lower price when they know who to call.  Opening up a phonebook, newspaper, or randomly selected online business could cost you hundreds, even thousands of dollars too much money.</p>
    <a class="abs btn" href="#">Know More</a>
    <div class="abs divider"></div>

    <h2 class="abs offer-title">WE OFFER</h2>
    <div class="abs offer" style="top:827px">
      <div class="pic" role="img" aria-label="Photo of a smiling man in a shirt and tie"></div>
      <div><h4>CALL ANSWERING SERVICES</h4><p>Accusamu dolore masugharum quidemed rerum facilis iustossi mos ducimus qui blanditiistes</p></div>
    </div>
    <div class="abs offer" style="top:906px">
      <div class="pic" role="img" aria-label="Photo of a person raising arms against the sky"></div>
      <div><h4>24/7 SUPPORT SERVICES</h4><p>Accusamu dolore masugharum quidemed rerum facilis iustossi mos ducimus qui blanditiistes</p></div>
    </div>
    <div class="abs offer" style="top:984px">
      <div class="pic" role="img" aria-label="Photo of a woman holding a tablet"></div>
      <div><h4>NETWORK MANAGEMENT</h4><p>Accusamu dolore masugharum quidemed rerum facilis iustossi mos ducimus qui blanditiistes</p></div>
    </div>
  </section>

  <footer>
    <div class="abs footer"></div>
    <div class="abs footer-brand"><span class="brand-dot"></span><span class="brand-name">Trueline</span></div>
    <p class="abs copyright">© copyrights Trueline Referral Hub Inc. All rights reserved</p>
    <nav class="abs footer-links">
      <a href="#">Home</a><a href="#">About trueline</a><a href="#">Services</a><a href="#">Our network</a><a href="#">Contact us</a>
    </nav>
    <div class="abs footer-contact">
      <div class="addr">450 Harbor Lane, Saint Louis, Missouri 63101</div>
      <div class="phone">Phone: 1-314-555-0142</div>
      <div class="mail">E-mail: info@truelinereferralhub.example</div>
    </div>
  </footer>

</div>
</body>
</html>
```